Walk Beside The River

Business Card design

Target Market(s)

People who require support in the commnity

Industry/Entity Type

Mental Health Support

Contact Information for Business Card

Mental Health Support Rosalind Tavener walkbesidetheriver@mailcove.com.au 0481 637 092 PO Box 926 Kelsworth QLD 4517

Colors
6B429C
8869AF
B7A5CE
E3DAEB
F3F0F8

Requirements
Must have
• Logo & details listed above
Should not have
• No red or orange

```html
<!DOCTYPE html>
<html lang="en">
<head>
<meta charset="utf-8">
<title>Walk Beside The River – Business Card</title>
<link rel="stylesheet" href="https://fonts.googleapis.com/css2?family=Lato:wght@400;700;900&display=swap">
<style>
  :root {
    --page-bg: #2a2a2c;
    --card-purple: #6d44a0;
    --sky-deep: #5a3690;
    --sky-mid: #7a45b4;
    --sky-light: #8869af;
    --accent-yellow: #f6e81f;
    --text-white: #ffffff;
  }
  * { box-sizing: border-box; margin: 0; padding: 0; }
  html, body {
    width: 1200px;
    height: 875px;
    overflow: hidden;
    background: var(--page-bg);
    font-family: "Lato", sans-serif;
  }
  .stage {
    width: 1200px;
    height: 875px;
    display: flex;
    align-items: center;
    justify-content: center;
    gap: 40px;
  }
  .card {
    position: relative;
    width: 540px;
    height: 309px;
    border-radius: 18px;
    overflow: hidden;
    flex: none;
  }

  /* Front */
  .card-front { background: var(--sky-deep); }
  .sky-texture {
    position: absolute;
    inset: 0;
    background:
      radial-gradient(ellipse 60% 40% at 40% 55%, rgba(150, 100, 200, 0.45), transparent 70%),
      radial-gradient(ellipse 50% 50% at 80% 30%, rgba(130, 70, 190, 0.5), transparent 70%),
      linear-gradient(135deg, var(--sky-deep) 0%, var(--sky-mid) 50%, var(--sky-deep) 100%);
  }
  .brand-lockup {
    position: absolute;
    inset: 0;
    display: flex;
    flex-direction: column;
    align-items: center;
    justify-content: center;
    gap: 16px;
  }
  .brand-dot {
    width: 46px;
    height: 46px;
    border-radius: 50%;
    background: var(--accent-yellow);
  }
  .brand-name {
    color: var(--text-white);
    font-weight: 700;
    font-size: 22px;
    letter-spacing: 0.22em;
    text-transform: uppercase;
  }

  /* Back */
  .card-back {
    background: var(--card-purple);
    display: flex;
    align-items: center;
    padding-left: 34px;
  }
  .identity {
    display: flex;
    flex-direction: column;
    align-items: flex-end;
  }
  .person-name {
    color: var(--accent-yellow);
    font-weight: 900;
    font-size: 26px;
    letter-spacing: -0.01em;
    text-transform: uppercase;
    line-height: 1;
    white-space: nowrap;
  }
  .person-role {
    color: var(--text-white);
    font-size: 15px;
    margin-top: 3px;
    white-space: nowrap;
  }
  .divider {
    width: 2px;
    height: 64px;
    background: var(--accent-yellow);
    margin: 0 14px;
    flex: none;
  }
  .contact-list {
    list-style: none;
    display: flex;
    flex-direction: column;
    gap: 5px;
  }
  .contact-item {
    display: flex;
    align-items: center;
    gap: 7px;
    color: var(--text-white);
    font-size: 11.5px;
    white-space: nowrap;
  }
  .contact-item.phone { font-size: 17px; font-weight: 700; }
  .contact-icon { width: 11px; height: 11px; flex: none; fill: var(--accent-yellow); }
</style>
</head>
<body>
<main class="stage">
  <section class="card card-front">
    <div class="sky-texture" role="img" aria-label="Soft purple night sky with faint stars"></div>
    <div class="brand-lockup">
      <span class="brand-dot"></span>
      <span class="brand-name">Walk Beside The River</span>
    </div>
  </section>

  <section class="card card-back">
    <div class="identity">
      <h1 class="person-name">Rosalind Tavener</h1>
      <p class="person-role">Mental Health Support</p>
    </div>
    <span class="divider"></span>
    <ul class="contact-list">
      <li class="contact-item phone">
        <svg class="contact-icon" viewBox="0 0 24 24"><path d="M6.6 10.8a15.1 15.1 0 0 0 6.6 6.6l2.2-2.2a1 1 0 0 1 1-.25 11.4 11.4 0 0 0 3.6.57 1 1 0 0 1 1 1V20a1 1 0 0 1-1 1A17 17 0 0 1 3 4a1 1 0 0 1 1-1h3.5a1 1 0 0 1 1 1c0 1.25.2 2.45.57 3.57a1 1 0 0 1-.25 1z"/></svg>
        0481 637 092
      </li>
      <li class="contact-item">
        <svg class="contact-icon" viewBox="0 0 24 24"><path d="M2 5h20v14H2z"/><path d="M2 5l10 8 10-8" fill="none" stroke="#6d44a0" stroke-width="2"/></svg>
        walkbesidetheriver@mailcove.com.au
      </li>
      <li class="contact-item">
        <svg class="contact-icon" viewBox="0 0 24 24"><path d="M12 2a7 7 0 0 0-7 7c0 5 7 13 7 13s7-8 7-13a7 7 0 0 0-7-7zm0 9.5A2.5 2.5 0 1 1 12 6.5a2.5 2.5 0 0 1 0 5z"/></svg>
        PO Box 926 Kelsworth QLD 4517
      </li>
    </ul>
  </section>
</main>
</body>
</html>
```